Brell Stone Company Business Cards

Front and Back Business Card - logo and text setup - cool design. I need workable photoshop or illustrator files so I can setup each employee card with design that is created
Updates

Hi everyone, thank you for the great entries. Please no more white and blue cards - there are so many already - black and silver only now please. thanks!

Target Market(s)

Construction Industry - Facility Managers

Industry/Entity Type

Construction

Contact Information for Business Card

I really like contemporary simplistic looks - clean neat....not opposed to seeing some black backrounds

Requirements
Must have
• Logo/website address with design on front only - www.brellstone-example.com (logo attached)
• Back:
• Name/Title/Company Address/Phone/email address
Nice to have
• Cool design
Should not have
• Nothing gimmicky like Fire or Water - since we are a Fire Protection company - it has all been done

```html
<!DOCTYPE html>
<html lang="en">
<head>
<meta charset="utf-8">
<title>Brell Stone Company – Business Cards</title>
<link rel="stylesheet" href="https://fonts.googleapis.com/css2?family=Montserrat:wght@400;500;700;800&display=swap">
<style>
  :root {
    --backdrop: #d9d9d9;
    --card-light: #ffffff;
    --card-dark: #4a4a4c;
    --ink-dark: #4a4a4c;
    --ink-light: #f2f2f2;
    --ink-muted: #d0d0d0;
    --shadow: rgba(0, 0, 0, 0.22);
  }
  * { margin: 0; padding: 0; box-sizing: border-box; }
  html, body { width: 1200px; height: 1200px; overflow: hidden; }
  body {
    background: var(--backdrop);
    font-family: "Montserrat", Arial, sans-serif;
    display: flex;
    flex-direction: column;
    align-items: center;
    justify-content: center;
    gap: 90px;
  }
  .card {
    position: relative;
    width: 760px;
    height: 434px;
    border-radius: 34px;
    box-shadow: 0 18px 40px var(--shadow);
    overflow: hidden;
  }

  /* Front */
  .card-front { background: var(--card-light); }
  .brand-name {
    position: absolute;
    right: 62px;
    top: 128px;
    font-size: 72px;
    font-weight: 800;
    letter-spacing: -2px;
    color: var(--ink-dark);
    line-height: 1;
  }
  .front-rule {
    position: absolute;
    left: 0;
    top: 300px;
    width: 72%;
    height: 9px;
    background: var(--ink-dark);
  }

  /* Back */
  .card-back { background: var(--card-dark); color: var(--ink-light); }
  .person {
    position: absolute;
    left: 300px;
    top: 110px;
  }
  .person-name {
    font-size: 38px;
    font-weight: 800;
    letter-spacing: 2px;
    line-height: 1.1;
  }
  .person-title {
    font-size: 22px;
    font-weight: 500;
    color: var(--ink-muted);
    margin-top: 4px;
  }
  .contact-row {
    position: absolute;
    left: 56px;
    right: 56px;
    bottom: 70px;
    display: flex;
    justify-content: space-between;
    align-items: flex-start;
  }
  .contact-item {
    display: flex;
    gap: 12px;
    align-items: flex-start;
    font-size: 15px;
    line-height: 1.4;
    color: var(--ink-muted);
  }
  .contact-icon { width: 18px; height: 18px; flex: none; margin-top: 2px; fill: var(--ink-light); }
</style>
</head>
<body>

  <section class="card card-front" aria-label="Business card front">
    <div class="brand-name">brellstone</div>
    <div class="front-rule"></div>
  </section>

  <section class="card card-back" aria-label="Business card back">
    <div class="person">
      <div class="person-name">MARCUS HALE</div>
      <div class="person-title">Facility Manager</div>
    </div>

    <div class="contact-row">
      <div class="contact-item">
        <svg class="contact-icon" viewBox="0 0 24 24" aria-hidden="true">
          <path d="M6.6 10.8a15.1 15.1 0 0 0 6.6 6.6l2.2-2.2a1 1 0 0 1 1-.25 11.4 11.4 0 0 0 3.6.57 1 1 0 0 1 1 1V20a1 1 0 0 1-1 1A17 17 0 0 1 3 4a1 1 0 0 1 1-1h3.5a1 1 0 0 1 1 1c0 1.25.2 2.45.57 3.6a1 1 0 0 1-.25 1z"/>
        </svg>
        <div>015 480 7721<br>012 480 3390</div>
      </div>
      <div class="contact-item">
        <svg class="contact-icon" viewBox="0 0 24 24" aria-hidden="true">
          <path d="M12 2a7 7 0 0 0-7 7c0 5.25 7 13 7 13s7-7.75 7-13a7 7 0 0 0-7-7zm0 9.5A2.5 2.5 0 1 1 12 6.5a2.5 2.5 0 0 1 0 5z"/>
        </svg>
        <div>#210 Quarry Ridge Rd,<br>Alden VA 22011</div>
      </div>
      <div class="contact-item">
        <svg class="contact-icon" viewBox="0 0 24 24" aria-hidden="true">
          <path d="M2 5h20v14H2z M2 5l10 8 10-8" fill="none" stroke="#f2f2f2" stroke-width="2"/>
        </svg>
        <div>info@brellstone-example.com<br>www.brellstone-example.com</div>
      </div>
    </div>
  </section>

</body>
</html>
```